Business Card Design needed - Something Awesome!

Need a business card designed. Company is "Marlowe Advisory" we do consulting and also have sales automation technology.
I'm going to use thick stock or metal, something really nice... I was thinking about a QR Code on the back that would just upload my contact info to the persons contact, etc -

This is a Strategy Company with a tech feel. I'm open to ideas but really want this to be nice!

I need a template that should include:

Name | Position or Title
D: 415.902.3376
www.marloweadvisory.example

I'm going to attach my contact so you can use that one, I need to get this printed.

Target Market(s)

Small to mid size customers, Entrepreneurs etc.

Industry/Entity Type

Consulting, Tech, Private Equity.

Contact Information for Business Card

Name, Phone, Maybe email, URL

Font styles to use
Sans Serif

Colors

Designer to choose only greyscale colors for use in the design.

Requirements
Must have
• Fresh, Clean, stand out from the crowd - will be on thick stock or metal.
Nice to have
• Clean, simple yet impactful.
Should not have
• Not cartoonish

```html
<!DOCTYPE html>
<html lang="en">
<head>
<meta charset="utf-8">
<title>Marlowe Advisory — Business Card</title>
<link rel="stylesheet" href="https://fonts.googleapis.com/css2?family=Montserrat:wght@300;400;600&display=swap">
<style>
  :root {
    --backdrop: #3b3b3b;
    --card: #121212;
    --silver: #cfcfcf;
    --silver-soft: #a9a9a9;
    --rule: #6a6a6a;
  }
  * { margin: 0; padding: 0; box-sizing: border-box; }
  html, body {
    width: 1200px; height: 801px; overflow: hidden;
    background: var(--backdrop);
    font-family: "Montserrat", sans-serif;
  }
  .sheet {
    width: 1200px; height: 801px;
    display: flex; align-items: center; justify-content: center; gap: 44px;
  }
  .card {
    position: relative;
    width: 520px; height: 297px;
    background: var(--card);
    border-radius: 3px;
    box-shadow: 0 18px 40px rgba(0,0,0,.45);
  }
  /* Front */
  .wordmark {
    position: absolute; left: 44px; top: 62px;
    font-weight: 300; font-size: 58px; letter-spacing: 4px;
    color: var(--silver);
  }
  .identity {
    position: absolute; left: 44px; top: 178px;
    width: 210px;
  }
  .identity .name {
    font-weight: 600; font-size: 17px; letter-spacing: .5px;
    color: var(--silver);
  }
  .identity .role {
    margin-top: 4px;
    font-weight: 400; font-size: 14px;
    color: var(--silver-soft);
  }
  .divider {
    position: absolute; left: 262px; top: 168px;
    width: 1px; height: 70px;
    background: var(--rule);
  }
  .contacts {
    position: absolute; left: 280px; top: 166px;
    list-style: none;
  }
  .contacts li {
    display: flex; align-items: center; gap: 8px;
    font-size: 12.5px; font-weight: 400; line-height: 24px;
    color: var(--silver);
  }
  .contacts svg { width: 11px; height: 11px; fill: var(--silver); flex: none; }
  /* Back */
  .back-mark {
    position: absolute; inset: 0;
    display: flex; align-items: center; justify-content: center; gap: 14px;
  }
  .back-mark .square {
    width: 22px; height: 22px; background: var(--silver);
  }
  .back-mark .label {
    font-weight: 300; font-size: 30px; letter-spacing: 3px;
    color: var(--silver);
  }
</style>
</head>
<body>
<main class="sheet">
  <section class="card card--front" aria-label="Card front">
    <div class="wordmark">MARLOWE</div>
    <div class="identity">
      <p class="name">JULIAN R. HALE</p>
      <p class="role">Founder / CEO</p>
    </div>
    <div class="divider"></div>
    <ul class="contacts">
      <li>
        <svg viewBox="0 0 24 24" aria-hidden="true"><path d="M6.6 10.8a15.1 15.1 0 0 0 6.6 6.6l2.2-2.2a1 1 0 0 1 1-.25 11.4 11.4 0 0 0 3.6.57 1 1 0 0 1 1 1V20a1 1 0 0 1-1 1A17 17 0 0 1 3 4a1 1 0 0 1 1-1h3.5a1 1 0 0 1 1 1c0 1.25.2 2.45.57 3.6a1 1 0 0 1-.25 1z"/></svg>
        415.902.3376
      </li>
      <li>
        <svg viewBox="0 0 24 24" aria-hidden="true"><path d="M2 5h20v14H2zM4 7v.5l8 5 8-5V7l-8 5z"/></svg>
        info@marloweadvisory.example
      </li>
      <li>
        <svg viewBox="0 0 24 24" aria-hidden="true"><path d="M12 2a10 10 0 1 0 0 20 10 10 0 0 0 0-20zm0 2c.9 0 2.2 1.9 2.7 5H9.3C9.8 5.9 11.1 4 12 4zM4.3 13a8 8 0 0 1 0-2h3v2zm.5 2h2.8a12 12 0 0 0 1.3 3.7A8 8 0 0 1 4.8 15zm2.8-6H4.8a8 8 0 0 1 4.1-3.7A12 12 0 0 0 7.6 9zM12 20c-.9 0-2.2-1.9-2.7-5h5.4c-.5 3.1-1.8 5-2.7 5zm-2.9-7v-2h5.8v2zm6 5.7a12 12 0 0 0 1.3-3.7h2.8a8 8 0 0 1-4.1 3.7zM16.7 13v-2h3a8 8 0 0 1 0 2zm-.3-4a12 12 0 0 0-1.3-3.7A8 8 0 0 1 19.2 9z"/></svg>
        www.marloweadvisory.example
      </li>
    </ul>
  </section>

  <section class="card card--back" aria-label="Card back">
    <div class="back-mark">
      <span class="square"></span>
      <span class="label">MARLOWE</span>
    </div>
  </section>
</main>
</body>
</html>
```